Christian Media Company Website

I am looking to design an easy to follow, sleek, creative website for my Christian video Bible study platform. On this platform you will be able to sign up to have access to dozens of free high-quality video Bible studies. With that being said There will be a total of 3 pages needed.

First, I will need the home page. This should contain all critical information to inform the customer. The design should be easy to follow, professional, and creative. I will post to some websites I like, if you just copy the website in your design will be removed immediately.

Secondly, we will need a landing Bible study page for people to look through the Bible studies to select one. I have uploaded Study images below with the aspect ratio I want for the design (for each Bible study image). There should be 2 sections Topical studies and Doctrinal Studies (with series under each section). I would like for people to be able to slide left or right through the studies under each category.

Lastly, we will need a video series page. This page needs to have the video they are watching, a playlist of the other videos, as well as a place to put the speaker's image and description. We will have studies that they can download so please make a place for this.

I will upload our color in the files along with our logo! Looking forward to seeing what you all will come up with!

Websites I like :
https://lanternvale.org/
https://www.quillharborfilms.org/
https://www.dunmorel.com/
https://tessavint.org/

Target Market(s)

Christians

Industry/Entity Type

Christian Video Design

Coding

Coded - Design and coding required

Number of Pages Required

3 page

Font styles to use
Sans Serif

Colors
00AB8E
00BBA5
67D7C9
C6EFE9
E9F9F6

Requirements
Should not have
• Pre-Used Templates

```html
<!DOCTYPE html>
<html lang="en">
<head>
<meta charset="utf-8">
<title>Lampstead Studies</title>
<link href="https://fonts.googleapis.com/css2?family=Poppins:wght@300;400;500;600;700&display=swap" rel="stylesheet">
<style>
:root{
  --teal:#2DC4AE;
  --teal-dark:#00AB8E;
  --teal-mid:#00BBA5;
  --teal-soft:#67D7C9;
  --mint:#E9F9F6;
  --ink:#1d1d1d;
  --text:#444;
  --muted:#777;
  --grey-band:#efefef;
  --white:#fff;
}
*{box-sizing:border-box;margin:0;padding:0}
html,body{width:1200px;height:3110px;overflow:hidden}
body{font-family:'Poppins',sans-serif;color:var(--ink);background:var(--white);position:relative}
.abs{position:absolute}
.btn{position:absolute;display:flex;align-items:center;justify-content:center;border-radius:5px;font-weight:500;font-size:16px}
.btn-solid{background:var(--teal);color:#123}
.btn-outline{border:1.5px solid var(--ink);color:var(--ink);background:transparent}

/* header + hero */
.hero{position:absolute;left:0;top:0;width:1200px;height:686px;
  background:linear-gradient(180deg,#d9a465 0%,#c68a55 30%,#9a6a4a 60%,#6e5344 100%)}
.hero-shade{position:absolute;inset:0;background:radial-gradient(ellipse at 50% 40%,rgba(255,210,140,.35),rgba(0,0,0,.15) 70%)}
.brand{position:absolute;left:112px;top:18px;display:flex;align-items:center;gap:10px;color:var(--teal);font-weight:600;font-size:21px;line-height:26px}
.brand-mark{width:44px;height:44px;border:3px solid var(--teal);border-radius:4px}
.nav{position:absolute;top:32px;left:624px;display:flex;gap:29px;font-size:16px;color:#222}
.nav .active{color:var(--teal);border-bottom:1.5px solid var(--teal);padding-bottom:2px}
.signup{left:963px;top:22px;width:124px;height:44px;border:1.5px solid var(--teal);color:var(--teal)}
.play{position:absolute;left:562px;top:206px;width:76px;height:76px;border-radius:50%;background:var(--teal)}
.hero-title{position:absolute;left:0;width:1200px;top:300px;text-align:center;color:#fff;font-weight:700;font-size:70px;letter-spacing:1px}
.hero-sub{position:absolute;left:0;width:1200px;top:388px;text-align:center;color:#fff;font-size:27px;font-weight:400}
.hero-cta{left:500px;top:448px;width:201px;height:49px}

/* about */
.hatch{position:absolute;left:834px;top:686px;width:366px;height:366px;
  background:repeating-linear-gradient(135deg,#ececec 0 1px,transparent 1px 7px)}
.about-kicker{left:114px;top:792px;font-size:26px;color:#222}
.about-title{left:114px;top:826px;font-size:43px;font-weight:600;color:var(--teal)}
.points{position:absolute;left:112px;top:908px;width:455px;list-style:none}
.points li{position:relative;padding-left:21px;font-size:14.5px;line-height:27.5px;color:var(--text);margin-bottom:18px}
.points li::before{content:"";position:absolute;left:1px;top:8px;width:11px;height:11px;border-radius:50%;background:var(--teal)}
.read-more{left:112px;top:1192px;width:200px;height:48px}
.frame{position:absolute;left:593px;top:786px;width:396px;height:370px;border:1.5px solid var(--teal-soft)}
.about-photo{position:absolute;left:617px;top:820px;width:471px;height:436px;
  background:linear-gradient(135deg,#3c4759 0%,#2a3140 45%,#6d8a86 100%)}

/* videos */
.videos{position:absolute;left:0;top:1348px;width:1200px;height:578px;background:var(--grey-band)}
.sec-title{position:absolute;left:0;width:1200px;text-align:center;font-size:43px;font-weight:600;color:#111}
.arrow{position:absolute;top:1610px}
.vcard{position:absolute;top:1491px;width:317px}
.thumb{position:relative;height:257px;border-radius:8px;overflow:hidden}
.thumb-1{background:linear-gradient(160deg,#4c4c4c,#8a8a8a)}
.thumb-2{background:linear-gradient(160deg,#3a3a3a,#b87a6f)}
.thumb-3{background:linear-gradient(160deg,#222,#6b6b6b)}
.thumb-label{position:absolute;left:12px;top:15px;color:#fff;font-size:12.5px}
.thumb-tools{position:absolute;right:18px;top:14px}
.thumb-play{position:absolute;left:140px;top:117px;width:37px;height:25px;border-radius:6px;background:#fff}
.author{display:flex;align-items:center;margin-top:12px;position:relative}
.avatar{width:54px;height:54px;border-radius:50%;background:linear-gradient(135deg,#c9a68a,#6b4c3b);margin-right:10px}
.author-name{font-size:14.5px;font-weight:500}
.author-role{font-size:11.5px;color:var(--muted)}
.kebab{position:absolute;right:18px;top:12px}
.vdesc{font-size:13.5px;line-height:26px;color:var(--text);margin-top:10px}

/* blog */
.bcard{position:absolute;top:2064px;width:318px;height:226px;border-radius:4px;background:#fff;
  box-shadow:0 0 5px rgba(0,0,0,.2);padding:22px 16px}
.bcard h3{font-size:16.5px;font-weight:500;margin-bottom:8px}
.bcard .date{font-size:14px;color:#333;margin-bottom:12px}
.bcard p{font-size:13.5px;line-height:27.5px;color:var(--muted)}

/* cta band */
.cta{position:absolute;left:0;top:2357px;width:1200px;height:350px;background:var(--mint)}
.cta h2{position:absolute;left:0;width:1200px;top:68px;text-align:center;font-size:33px;font-weight:600}
.cta p{position:absolute;left:200px;width:800px;top:118px;text-align:center;font-size:15.5px;line-height:30px;color:#333}
.cta-a{left:391px;top:226px;width:201px;height:50px}
.cta-b{left:608px;top:226px;width:202px;height:50px}

/* footer */
.fcol{position:absolute;top:2778px}
.fcol h4{font-size:16.5px;font-weight:500;margin-bottom:26px}
.fcol ul{list-style:none}
.fcol li{font-size:13.5px;color:#333;line-height:16px;margin-bottom:16px;padding-left:14px;position:relative}
.fcol li::before{content:"›";position:absolute;left:0;top:-1px;font-size:15px}
.fdiv{position:absolute;top:2787px;width:1px;height:176px;background:#ddd}
.fbrand{left:842px;top:2778px}
.contact{position:absolute;left:848px;font-size:14px;color:#333;line-height:23px}
.contact svg{position:absolute;left:0;top:5px}
.contact span{display:block;padding-left:22px}
.rule{position:absolute;left:110px;top:3016px;width:978px;height:1px;background:#ddd}
.copy{left:110px;top:3052px;font-size:15.5px;color:#333}
.legal{left:776px;top:3054px;font-size:14px;color:#333;width:312px;text-align:right}
</style>
</head>
<body>

<section class="hero" role="img" aria-label="Photo of friends laughing together on a beach at sunset">
  <div class="hero-shade"></div>
</section>
<div class="brand"><div class="brand-mark"></div><div>LAMPSTEAD<br>STUDIES</div></div>
<nav class="nav"><span class="active">Home</span><span>About Us</span><span>Videos</span><span>Contact</span></nav>
<div class="btn signup">Signup</div>
<div class="play"><svg width="76" height="76" viewBox="0 0 76 76"><path d="M30 25 L52 38 L30 51Z" fill="#fff"/></svg></div>
<h1 class="hero-title">LAMPSTEAD STUDIES</h1>
<div class="hero-sub">Christian video Bible study platform</div>
<div class="btn btn-solid hero-cta">Get Started</div>
<svg class="abs" style="left:589px;top:627px" width="22" height="14" viewBox="0 0 22 14"><path d="M3 3 L11 11 L19 3" fill="none" stroke="#fff" stroke-width="2"/></svg>

<div class="hatch"></div>
<div class="abs about-kicker">About</div>
<h2 class="abs about-title">Lampstead Studies</h2>
<ul class="points">
  <li>Lorem ipsum dolor sit amet, consectetur adipiscing elit, sed do eiusmod tempor incididunt ut labore et dolore magna aliqua. Ut enim ad minim veniam,</li>
  <li>Lorem ipsum dolor sit amet, consectetur adipiscing elit, sed do eiusmod tempor incididunt ut labore et dolore magna aliqua. Ut enim ad minim veniam,</li>
  <li>Lorem ipsum dolor sit amet, consectetur adipiscing elit, sed do eiusmod tempor incididunt ut labore et dolore</li>
</ul>
<div class="btn btn-solid read-more">Read More</div>
<div class="frame"></div>
<div class="about-photo" role="img" aria-label="Photo of a Bible beside a phone streaming an audio Bible"></div>

<section class="videos"></section>
<h2 class="sec-title" style="top:1396px">Our Videos</h2>
<svg class="arrow" style="left:64px" width="20" height="30" viewBox="0 0 20 30"><path d="M15 4 L5 15 L15 26" fill="none" stroke="#222" stroke-width="2.5"/></svg>
<svg class="arrow" style="left:1116px" width="20" height="30" viewBox="0 0 20 30"><path d="M5 4 L15 15 L5 26" fill="none" stroke="#222" stroke-width="2.5"/></svg>

<article class="vcard" style="left:103px">
  <div class="thumb thumb-1" role="img" aria-label="Video still of a speaker with a title overlay">
    <div class="thumb-label">Lorem ipsum dolor sit amet</div>
    <svg class="thumb-tools" width="36" height="14" viewBox="0 0 36 14"><path d="M6 1v8M2 6l4 4 4-4M1 13h10" stroke="#fff" stroke-width="1.6" fill="none"/><path d="M24 12c0-5 3-7 8-7M29 2l3 3-3 3" stroke="#fff" stroke-width="1.6" fill="none"/></svg>
    <div class="thumb-play"><svg width="37" height="25"><path d="M15 7l8 5.5-8 5.5z" fill="#222"/></svg></div>
  </div>
  <div class="author"><div class="avatar"></div><div><div class="author-name">Marla Quenby</div><div class="author-role">Lorem ipsum</div></div>
    <svg class="kebab" width="6" height="26"><circle cx="3" cy="3" r="2.5" fill="#999"/><circle cx="3" cy="13" r="2.5" fill="#999"/><circle cx="3" cy="23" r="2.5" fill="#999"/></svg></div>
  <p class="vdesc">Lorem ipsum dolor sit amet, adipiscing elit, sed do eiusmod tempor incididunt ut</p>
</article>
<article class="vcard" style="left:442px">
  <div class="thumb thumb-2" role="img" aria-label="Video still of a speaker with a title overlay">
    <div class="thumb-label">Lorem ipsum dolor sit amet</div>
    <svg class="thumb-tools" width="36" height="14" viewBox="0 0 36 14"><path d="M6 1v8M2 6l4 4 4-4M1 13h10" stroke="#fff" stroke-width="1.6" fill="none"/><path d="M24 12c0-5 3-7 8-7M29 2l3 3-3 3" stroke="#fff" stroke-width="1.6" fill="none"/></svg>
    <div class="thumb-play"><svg width="37" height="25"><path d="M15 7l8 5.5-8 5.5z" fill="#222"/></svg></div>
  </div>
  <div class="author"><div class="avatar"></div><div><div class="author-name">Dorian Pell</div><div class="author-role">Lorem ipsum</div></div>
    <svg class="kebab" width="6" height="26"><circle cx="3" cy="3" r="2.5" fill="#999"/><circle cx="3" cy="13" r="2.5" fill="#999"/><circle cx="3" cy="23" r="2.5" fill="#999"/></svg></div>
  <p class="vdesc">Lorem ipsum dolor sit amet, adipiscing elit, sed do eiusmod tempor incididunt ut</p>
</article>
<article class="vcard" style="left:780px">
  <div class="thumb thumb-3" role="img" aria-label="Video still of a speaker with a title overlay">
    <div class="thumb-label">Lorem ipsum dolor sit amet</div>
    <svg class="thumb-tools" width="36" height="14" viewBox="0 0 36 14"><path d="M6 1v8M2 6l4 4 4-4M1 13h10" stroke="#fff" stroke-width="1.6" fill="none"/><path d="M24 12c0-5 3-7 8-7M29 2l3 3-3 3" stroke="#fff" stroke-width="1.6" fill="none"/></svg>
    <div class="thumb-play"><svg width="37" height="25"><path d="M15 7l8 5.5-8 5.5z" fill="#222"/></svg></div>
  </div>
  <div class="author"><div class="avatar"></div><div><div class="author-name">Silas Verrow</div><div class="author-role">Lorem ipsum</div></div>
    <svg class="kebab" width="6" height="26"><circle cx="3" cy="3" r="2.5" fill="#999"/><circle cx="3" cy="13" r="2.5" fill="#999"/><circle cx="3" cy="23" r="2.5" fill="#999"/></svg></div>
  <p class="vdesc">Lorem ipsum dolor sit amet, adipiscing elit, sed do eiusmod tempor incididunt ut</p>
</article>

<h2 class="sec-title" style="top:1984px">Our Blog</h2>
<article class="bcard" style="left:111px"><h3>Lorem ipsum dolor sit amet,</h3><div class="date">25-10-2021</div><p>Lorem ipsum dolor sit amet, consectetur adipiscing elit, sed do eiusmod tempor incididunt ut labore et dolore magna aliqua. Ut enim ad minim veniam,</p></article>
<article class="bcard" style="left:441px"><h3>Lorem ipsum dolor sit amet,</h3><div class="date">25-10-2021</div><p>Lorem ipsum dolor sit amet, consectetur adipiscing elit, sed do eiusmod tempor incididunt ut labore et dolore magna aliqua. Ut enim ad minim veniam,</p></article>
<article class="bcard" style="left:771px"><h3>Lorem ipsum dolor sit amet,</h3><div class="date">25-10-2021</div><p>Lorem ipsum dolor sit amet, consectetur adipiscing elit, sed do eiusmod tempor incididunt ut labore et dolore magna aliqua. Ut enim ad minim veniam,</p></article>

<section class="cta">
  <h2>Lorem ipsum dolor sit amet</h2>
  <p>Lorem ipsum dolor sit amet, consectetur adipiscing elit, sed do eiusmod tempor incididunt ut labore et dolore magna aliqua. Ut enim ad minim veniam, quis nostrud exercitation ullamco laboris nisi ut aliquip ex ea commodo consequat. Duis aute irure dolor in reprehenderit in voluptate velit esse cillum</p>
  <div class="btn btn-solid cta-a">Topical studies</div>
  <div class="btn btn-outline cta-b">Doctrinal Studies</div>
</section>

<div class="fcol" style="left:138px"><h4>Menu</h4><ul><li>Home</li><li>About Us</li><li>Videos</li><li>Contact</li></ul></div>
<div class="fdiv" style="left:280px"></div>
<div class="fcol" style="left:338px"><h4>About Us</h4><ul><li>Mission</li><li>President's Story</li><li>Doctrinal Statement</li><li>Selecting Content</li></ul></div>
<div class="fdiv" style="left:541px"></div>
<div class="fcol" style="left:594px"><h4>More Info</h4><ul><li>Launch Resources</li><li>App Features</li><li>Virtual Groups</li><li>Stories</li><li>Pricing</li></ul></div>
<div class="fdiv" style="left:792px"></div>
<div class="brand" style="left:842px;top:2780px;font-size:17px;line-height:22px"><div class="brand-mark" style="width:38px;height:38px"></div><div>LAMPSTEAD<br>STUDIES</div></div>
<div class="contact" style="top:2858px"><svg width="15" height="12" viewBox="0 0 15 12"><rect x="0" y="0" width="15" height="12" rx="1" fill="var(--teal)"/><path d="M1 1l6.5 5L14 1" stroke="#fff" fill="none"/></svg><span>info@lampsteadstudies.org</span></div>
<div class="contact" style="top:2890px"><svg width="14" height="14" viewBox="0 0 14 14"><path d="M3 1l3 3-2 2c1 2 2 3 4 4l2-2 3 3-2 2C6 13 1 8 1 3z" fill="var(--teal)"/></svg><span>+1 888-888-8888</span></div>
<div class="contact" style="top:2922px"><svg width="12" height="15" viewBox="0 0 12 15"><path d="M6 0a5 5 0 0 1 5 5c0 4-5 10-5 10S1 9 1 5a5 5 0 0 1 5-5z" fill="var(--teal)"/><circle cx="6" cy="5" r="2" fill="#fff"/></svg><span>Lorem ipsum dolor sit amet,<br>consectetur adipiscing</span></div>

<div class="rule"></div>
<div class="abs copy">© 2022All Rights Reserved</div>
<div class="abs legal">Terms of Use | Contact Us | Privacy Statement</div>

</body>
</html>
```